Marlowe Group needs a business card

I would like the card to be simple but modern and elegant.
I like black and white.
or black and gold.
we are a private finance lender and also are involved in property and property developments.

please look at the business card photos i provided i would like M.G only one one side and all the other details on the other side use fonts that tie in with my theme.

Industry/Entity Type

Finance

Contact Information for Business Card

Marlowe Group (M.G) Daniel Marlowe M: 0413586207 E: danmarl@inboxmail.test

Font styles to use
Other font styles liked:
• Use fonts that would reflect our business

Colors
000000
ffffff

Requirements
Must have
• one side of details
• other side has either M.G or Marlowe Group like in the photos provided

```html
<!DOCTYPE html>
<html lang="en">
<head>
<meta charset="utf-8">
<title>Marlowe Group — Business Card</title>
<link href="https://fonts.googleapis.com/css2?family=Cinzel:wght@400;700&family=Lato:wght@400&display=swap" rel="stylesheet">
<style>
  :root {
    --backdrop: #808080;
    --ink: #000000;
    --gold: #ffcb3b;
    --gold-light: #fde6a3;
    --gold-text: #f7c634;
    --white: #ffffff;
  }
  * { margin: 0; padding: 0; box-sizing: border-box; }
  html, body { width: 1200px; height: 900px; overflow: hidden; }
  body { background: var(--backdrop); position: relative; font-family: "Lato", sans-serif; }

  .card {
    position: absolute;
    top: 271px;
    width: 457px;
    height: 282px;
    border-radius: 14px;
    overflow: hidden;
    box-shadow: 2px 3px 5px rgba(0,0,0,0.35);
  }

  /* Details side */
  .card--details { left: 137px; background: var(--ink); }
  .details__band {
    position: absolute; top: 0; right: 0; width: 115px; height: 100%;
    background: linear-gradient(90deg, var(--gold) 0%, var(--gold) 55%, var(--gold-light) 85%, var(--gold) 100%);
  }
  .details__tab {
    position: absolute; top: 72px; left: 279px; width: 140px; height: 135px;
    background: var(--ink);
    display: flex; align-items: center; justify-content: center;
  }
  .details__mark {
    font-family: "Cinzel", serif; font-weight: 400; font-size: 40px;
    color: var(--gold-text); letter-spacing: 2px;
  }
  .details__company {
    position: absolute; left: 37px; top: 34px;
    font-family: "Cinzel", serif; font-size: 25px; font-weight: 400;
    color: var(--gold-text); letter-spacing: 0.5px;
  }
  .details__name {
    position: absolute; left: 37px; top: 156px;
    font-family: "Cinzel", serif; font-size: 17px; font-weight: 700;
    color: var(--gold-text);
  }
  .details__contacts { position: absolute; left: 37px; top: 202px; list-style: none; }
  .details__contacts li {
    display: flex; align-items: center; gap: 8px;
    font-size: 14px; color: var(--white); line-height: 19px;
  }
  .details__contacts svg { width: 9px; height: 11px; fill: var(--gold-text); }

  /* Brand side */
  .card--brand {
    left: 626px;
    background: linear-gradient(90deg, var(--gold) 0%, var(--gold) 38%, var(--gold-light) 60%, var(--gold-light) 66%, var(--gold) 88%, var(--gold) 100%);
    display: flex; flex-direction: column; align-items: center; justify-content: center;
  }
  .brand__mark {
    font-family: "Cinzel", serif; font-weight: 400; font-size: 62px;
    color: var(--ink); letter-spacing: 3px; line-height: 1;
    margin-left: 0; margin-top: 10px;
  }
  .brand__name {
    font-family: "Cinzel", serif; font-size: 21px; font-weight: 400;
    color: var(--ink); margin-top: 26px;
  }
</style>
</head>
<body>
  <section class="card card--details">
    <div class="details__band"></div>
    <div class="details__tab"><span class="details__mark">M.G</span></div>
    <h1 class="details__company">Marlowe Group</h1>
    <p class="details__name">Daniel Marlowe</p>
    <ul class="details__contacts">
      <li>
        <svg viewBox="0 0 9 11" aria-hidden="true"><path d="M1.5 0h6a1 1 0 0 1 1 1v9a1 1 0 0 1-1 1h-6a1 1 0 0 1-1-1V1a1 1 0 0 1 1-1zm.5 1.5v6.5h5V1.5zM4.5 8.7a.7.7 0 1 0 0 1.4.7.7 0 0 0 0-1.4z"/></svg>
        0413586207
      </li>
      <li>
        <svg viewBox="0 0 9 11" aria-hidden="true"><path d="M0 3h9v6H0zM.6 3.4 4.5 6.3 8.4 3.4" stroke="#000" stroke-width="0.8"/></svg>
        danmarl@inboxmail.test
      </li>
    </ul>
  </section>

  <section class="card card--brand">
    <span class="brand__mark">M.G</span>
    <p class="brand__name">Marlowe Group</p>
  </section>
</body>
</html>
```